Cleaning Service Company In need of Good Web presence.

The company is a cleaning service company which provides professional staff and service for cleaning. This is a project to build a site that is both solid and a strong recognition of our organization. It is supposed to show quality, cleanliness, professionalism. The use of images and art for imagery is all good just to have a site that is consistent and solid. There might be a chance to make stationary, logo and business cars if someone feels they can build a brand that is consistent. The image we are going for is clean solid and to stand out. Finally stationary should not be expensive to print.

Current logo is attached and can be used or can be made more creative.

Target Market(s)

Corporate and Government entities, that will feel that this company has a brand that sets it apart from the rest. The company is new so the modification of the logo will not be an issue if a more solid brand come out of this project. The idea is to have a clean consistent product that stands our from others in terms of website, stationary, etc

Industry/Entity Type

Cleaning Service

Contact Information for Business Card

P.O.Box 51947
Riffa
Kingdom of Bahrain

Logo Text

Harbor Lane Services

Number of Pages Required

4 page

Font styles to use
Sans Serif

Colors
abd036
cadf82
eaf2ce
9bcb3b

Requirements
Must have
• Green Color to be used in order to stick to the name. Also the creativity and boldness in an elegant manner.
Nice to have
• Arabic name of company
• هاربر لين سرفسس ذ.م.م
• if cannot be put at least make a location should be chosen
• Also could be a bit of 3D given to the logo if it could stay elegent.
Should not have
• Should not show people cleaning.

```html
<!DOCTYPE html>
<html lang="en">
<head>
<meta charset="utf-8">
<title>Harbor Lane Services</title>
<link href="https://fonts.googleapis.com/css2?family=Poppins:wght@400;600;700&family=Roboto:wght@400;500&family=Tajawal:wght@700&display=swap" rel="stylesheet">
<style>
:root{
  --green:#abd036;
  --green-deep:#9bcb3b;
  --green-dark:#8cb22b;
  --green-soft:#cadf82;
  --green-pale:#eaf2ce;
  --ink:#333333;
  --body:#6b6b6b;
  --band:#f7f7f7;
  --white:#ffffff;
}
*{margin:0;padding:0;box-sizing:border-box}
html,body{width:752px;height:1200px;overflow:hidden;background:var(--white)}
body{position:relative;font-family:'Poppins',sans-serif;color:var(--body)}
.abs{position:absolute}

/* Top bar */
.topbar{left:0;top:0;width:752px;height:36px;background:var(--green)}
.menu{left:61px;top:11px;color:var(--white);font:500 8.5px 'Roboto',sans-serif;display:flex;align-items:center;gap:7px}
.menu-icon{width:8px;height:7px;display:flex;flex-direction:column;justify-content:space-between}
.menu-icon span{display:block;height:1.5px;background:var(--white)}
.btn-callback{left:491px;top:7px;width:95px;height:22px;border:1px solid var(--white);color:var(--white);font:400 8px 'Roboto',sans-serif;display:flex;align-items:center;justify-content:center}
.btn-quote{left:595px;top:7px;width:94px;height:22px;background:var(--green-dark);color:var(--white);font:500 8px 'Roboto',sans-serif;display:flex;align-items:center;justify-content:center}

/* Hero */
.hero{left:0;top:36px;width:752px;height:338px;background:linear-gradient(160deg,#8c969c 0%,#5b656c 40%,#3f474d 75%,#2f363b 100%)}
.hero-brand{left:0;top:86px;width:752px;display:flex;align-items:center;justify-content:center;gap:8px;color:var(--white);font:600 15px 'Poppins',sans-serif}
.brand-dot{width:14px;height:14px;border-radius:50%;background:var(--green)}
.hero-arabic{left:0;top:200px;width:752px;text-align:center;color:var(--white);font:700 20px 'Tajawal',sans-serif}
.hero-title{left:0;top:240px;width:752px;text-align:center;color:var(--white);font:700 23.5px 'Poppins',sans-serif;letter-spacing:.4px}
.hero-cta{left:298px;top:295px;width:145px;height:30px;border:2px solid var(--white);color:var(--white);font:500 12.5px 'Roboto',sans-serif;display:flex;align-items:center;justify-content:center;letter-spacing:.2px}

/* Welcome */
.welcome-title{left:0;top:396px;width:752px;text-align:center;color:var(--green-deep);font:500 25px 'Roboto',sans-serif}
.welcome-text{left:90px;top:439px;width:572px;text-align:center;font-size:6.6px;line-height:12.8px}
.feature{width:190px}
.feature-head{display:flex;align-items:center;gap:8px;color:var(--ink);font:500 12.4px 'Roboto',sans-serif;height:36px}
.feature-head svg{flex:none}
.feature-text{margin-left:27px;font-size:6.4px;line-height:12.8px;text-align:justify;width:150px}

/* Services */
.services{left:0;top:634px;width:752px;height:252px;background:var(--band)}
.services-title{left:0;top:658px;width:752px;text-align:center;color:var(--green-deep);font:500 18.5px 'Roboto',sans-serif}
.services-text{left:86px;top:693px;width:580px;text-align:center;font-size:6.5px;line-height:12.8px}
.service{width:175px}
.service-head{display:flex;align-items:flex-end;gap:7px;color:var(--ink);font:400 13px 'Roboto',sans-serif;height:30px}
.service-text{margin-top:8px;font-size:6.4px;line-height:12.4px;text-align:justify;width:160px}
.pager{left:705px;top:802px;display:flex;flex-direction:column;gap:3px}
.pager span{width:6px;height:6px;border:1px solid var(--green-dark);border-radius:50%}
.pager span.on{background:radial-gradient(circle,var(--green-dark) 40%,transparent 45%)}

/* Testimonials */
.clients-title{left:0;top:910px;width:752px;text-align:center;color:var(--green-deep);font:500 15.5px 'Roboto',sans-serif}
.clients-text{left:170px;top:938px;width:412px;text-align:center;font-size:6.5px;line-height:12.8px}
.portrait{top:978px;width:173px;height:163px}
.portrait-a{left:93px;background:linear-gradient(150deg,#9a9a98,#6f706d 60%,#4f8da6)}
.portrait-b{left:289px;background:linear-gradient(160deg,#c9d38e,#b7c27a 55%,#a2ad63)}
.portrait-c{left:489px;background:linear-gradient(150deg,#d5d6d8,#a7a9ac 55%,#7690a8)}
.portrait-name{left:289px;top:1083px;width:173px;text-align:center;color:var(--white);font:700 14px 'Poppins',sans-serif;letter-spacing:2.5px}
.portrait-social{left:289px;top:1113px;width:173px;display:flex;justify-content:center;gap:13px}
.portrait-social span{width:9px;height:9px;border-radius:50%;background:var(--white)}

/* Footer */
.footer{left:0;top:1168px;width:752px;height:32px;background:var(--green);color:var(--white);font:500 7.5px 'Poppins',sans-serif;display:flex;align-items:center;justify-content:center}
</style>
</head>
<body>

<header class="abs topbar"></header>
<div class="abs menu"><div class="menu-icon"><span></span><span></span><span></span></div>Menu</div>
<div class="abs btn-callback">Request A Call Back</div>
<div class="abs btn-quote">Book A Quote</div>

<section class="abs hero" role="img" aria-label="Photo of a polished tiled floor with a floor-cleaning machine"></section>
<div class="abs hero-brand"><span class="brand-dot"></span>Harbor Lane Services</div>
<div class="abs hero-arabic" dir="rtl" lang="ar">هاربر لين سرفسس ذ.م.م</div>
<h1 class="abs hero-title">High Quality Cleaning Services</h1>
<div class="abs hero-cta">CALL US TODAY</div>

<h2 class="abs welcome-title">Welcome To Harbor Lane Services</h2>
<p class="abs welcome-text">Harbor Lane Services keeps offices, homes and public buildings spotless with trained teams, safe products and careful planning. We work to a clear schedule, check every room before we leave and report back after each visit. Our staff arrive on time, wear clean uniforms and treat every space with respect. From single visits to long term contracts, we shape each plan around your building, your hours and your budget, so you always get a bright, fresh place to work and live.</p>

<div class="abs feature" style="left:62px;top:512px">
  <div class="feature-head">
    <svg width="19" height="36" viewBox="0 0 19 36" fill="none" stroke="#9bcb3b" stroke-width="1.3"><path d="M4 2h8l4 4h-4v5h-6V2z"/><path d="M6 11h6l3 6v16a2 2 0 0 1-2 2H5a2 2 0 0 1-2-2V17z"/><path d="M5 22h10"/></svg>
    Quality Cleaning
  </div>
  <p class="feature-text">Trained teams use tested methods and safe products on every surface, from glass and steel to wood and stone, leaving each room fresh, bright and ready to use.</p>
</div>
<div class="abs feature" style="left:275px;top:512px">
  <div class="feature-head">
    <svg width="38" height="36" viewBox="0 0 38 36" fill="none" stroke="#9bcb3b" stroke-width="1.4"><path d="M18 30V14a8 8 0 0 1 16 0v16z"/><circle cx="28" cy="28" r="3.5"/><path d="M18 16Q8 18 6 32"/><path d="M2 32h8"/></svg>
    Professional Staff
  </div>
  <p class="feature-text">Trained teams use tested methods and safe products on every surface, from glass and steel to wood and stone, leaving each room fresh, bright and ready to use.</p>
</div>
<div class="abs feature" style="left:505px;top:505px">
  <div class="feature-head" style="height:48px">
    <svg width="30" height="46" viewBox="0 0 30 46" fill="none" stroke="#9bcb3b" stroke-width="1.3"><path d="M12 2l10 40"/><path d="M18 42h10"/><path d="M2 28h14v16H2z"/><circle cx="5" cy="22" r="2"/><circle cx="10" cy="20" r="1.5"/></svg>
    Affordable Rates
  </div>
  <p class="feature-text">Trained teams use tested methods and safe products on every surface, from glass and steel to wood and stone, leaving each room fresh, bright and ready to use.</p>
</div>

<section class="abs services"></section>
<h2 class="abs services-title">Our Services</h2>
<p class="abs services-text">We offer a full range of cleaning for offices, homes and public buildings, planned around your hours. Every job is checked by a supervisor, and every client gets one contact person who knows the site, the team and the plan from start to finish.</p>

<div class="abs service" style="left:78px;top:760px">
  <div class="service-head">
    <svg width="22" height="24" viewBox="0 0 22 24" fill="none" stroke="#9bcb3b" stroke-width="1.4"><path d="M20 2L12 14"/><path d="M2 20q4-8 12-6l-2 6z"/></svg>
    Move In &amp; Out Cleaning
  </div>
  <p class="service-text">Our crews clean every corner, floor and fitting before you move in or after you move out, so the keys change hands with the space spotless.</p>
</div>
<div class="abs service" style="left:294px;top:760px">
  <div class="service-head">
    <svg width="22" height="22" viewBox="0 0 22 22" fill="#9bcb3b"><path d="M11 1L1 6h20z"/><rect x="2" y="7" width="18" height="2"/><rect x="4" y="10" width="2.5" height="7"/><rect x="9.7" y="10" width="2.5" height="7"/><rect x="15.5" y="10" width="2.5" height="7"/><rect x="1" y="18" width="20" height="3"/></svg>
    Office Cleaning
  </div>
  <p class="service-text">Our crews clean every corner, floor and fitting before you move in or after you move out, so the keys change hands with the space spotless.</p>
</div>
<div class="abs service" style="left:511px;top:757px">
  <div class="service-head" style="height:33px">
    <svg width="30" height="31" viewBox="0 0 30 31" fill="none" stroke="#9bcb3b" stroke-width="1.2"><rect x="1" y="14" width="8" height="16"/><rect x="10" y="8" width="8" height="22"/><rect x="19" y="2" width="10" height="28"/><path d="M3 14v-4h4v4M12 8V4h4v4"/></svg>
    Deep Cleaning
  </div>
  <p class="service-text">Our crews clean every corner, floor and fitting before you move in or after you move out, so the keys change hands with the space spotless.</p>
</div>
<div class="abs pager"><span class="on"></span><span></span><span></span></div>

<h2 class="abs clients-title">What Client Say’s About Us</h2>
<p class="abs clients-text">Our clients trust us with their offices, homes and public spaces. Here is what a few of them say about the care and results our teams deliver.</p>

<div class="abs portrait portrait-a" role="img" aria-label="Portrait photo of a smiling client"></div>
<div class="abs portrait portrait-b" role="img" aria-label="Portrait photo of a smiling client with a green overlay"></div>
<div class="abs portrait-name">MARLA VOSS</div>
<div class="abs portrait-social"><span></span><span></span><span></span></div>
<div class="abs portrait portrait-c" role="img" aria-label="Portrait photo of a smiling client"></div>

<footer class="abs footer">© 2017 Harbor Lane Services. All Rights Reserved.</footer>

</body>
</html>
```